Business Card for a New Zealand IT Startup

I need a business card for VELTA Holdings. We are a young startup based in New Zealand working in internet marketing and web development. The design should have some element connected to New Zealand, such as wave, koru or silver fern, just don't use a kiwi bird.

```html
<!DOCTYPE html>
<html lang="en">
<head>
<meta charset="utf-8">
<title>VELTA Holdings — Business Card</title>
<link rel="stylesheet" href="https://fonts.googleapis.com/css2?family=Open+Sans:wght@400;600&display=swap">
<style>
  :root {
    --brand-blue: #0b6fbf;
    --brand-blue-deep: #075fa8;
    --accent-orange: #f0642d;
    --paper: #ffffff;
    --backdrop: #e9e7e3;
  }
  * { box-sizing: border-box; margin: 0; padding: 0; }
  html, body { width: 1200px; height: 1040px; overflow: hidden; }
  body {
    background: var(--backdrop);
    font-family: "Open Sans", Arial, sans-serif;
    position: relative;
  }
  .card {
    position: absolute;
    left: 180px;
    width: 840px;
    height: 480px;
    box-shadow: 0 10px 28px rgba(0,0,0,.18);
    overflow: hidden;
  }
  /* Front side */
  .card--front { top: 30px; display: flex; background: var(--paper); }
  .front__brand {
    width: 430px;
    display: flex;
    align-items: center;
    justify-content: center;
    gap: 18px;
  }
  .brand-dot {
    width: 46px; height: 46px; border-radius: 50%;
    background: var(--brand-blue);
  }
  .brand-name {
    color: var(--brand-blue);
    font-weight: 600;
    font-size: 40px;
    letter-spacing: 1px;
  }
  .front__divider { width: 4px; background: var(--accent-orange); }
  .front__details {
    flex: 1;
    background: linear-gradient(160deg, #2f8fd6 0%, var(--brand-blue) 45%, var(--brand-blue-deep) 100%);
    color: var(--paper);
    padding: 70px 0 0 56px;
  }
  .person-name { font-size: 34px; font-weight: 600; letter-spacing: .5px; line-height: 1.1; }
  .person-title { font-size: 24px; font-weight: 400; margin-bottom: 22px; }
  .address { font-size: 21px; line-height: 1.3; margin-bottom: 16px; }
  .contact-list { list-style: none; font-size: 21px; line-height: 1.45; }
  .contact-list li { display: flex; align-items: center; gap: 12px; }
  .contact-list svg { width: 18px; height: 18px; flex: none; }

  /* Back side */
  .card--back {
    top: 530px;
    background: var(--brand-blue);
    border-radius: 34px;
    color: var(--paper);
  }
  .back__web {
    position: absolute;
    top: 46px; left: 60px;
    font-size: 20px;
    letter-spacing: 9px;
  }
  .back__brand {
    position: absolute;
    inset: 0;
    display: flex;
    align-items: center;
    justify-content: center;
    gap: 22px;
  }
  .back__brand .brand-dot { background: var(--paper); width: 60px; height: 60px; }
  .back__brand .brand-name { color: var(--paper); font-size: 48px; }
</style>
</head>
<body>

<section class="card card--front" aria-label="Business card front">
  <div class="front__brand">
    <span class="brand-dot"></span>
    <span class="brand-name">VELTA Holdings</span>
  </div>
  <div class="front__divider"></div>
  <div class="front__details">
    <p class="person-name">MARA QUINN</p>
    <p class="person-title">CEO/FOUNDER</p>
    <p class="address">42 Harbour Street<br>Wellington, NZ 6011</p>
    <ul class="contact-list">
      <li>
        <svg viewBox="0 0 24 24" fill="#fff"><path d="M6.6 10.8a15 15 0 0 0 6.6 6.6l2.2-2.2a1 1 0 0 1 1-.25 11.4 11.4 0 0 0 3.6.57 1 1 0 0 1 1 1V20a1 1 0 0 1-1 1A17 17 0 0 1 3 4a1 1 0 0 1 1-1h3.5a1 1 0 0 1 1 1c0 1.25.2 2.450.57 3.57a1 1 0 0 1-.25 1z"/></svg>
        021 583 7160
      </li>
      <li>
        <svg viewBox="0 0 24 24" fill="none" stroke="#fff" stroke-width="2.4"><rect x="6" y="2" width="12" height="20" rx="2"/></svg>
        022 914 2075
      </li>
      <li>
        <svg viewBox="0 0 24 24" fill="#fff"><rect x="3" y="9" width="18" height="10" rx="1"/><rect x="7" y="3" width="10" height="6"/></svg>
        04 762 3819
      </li>
      <li>
        <svg viewBox="0 0 24 24"><rect x="2" y="5" width="20" height="14" fill="#fff"/><path d="M2 5l10 8 10-8" fill="none" stroke="#0b6fbf" stroke-width="2"/></svg>
        mara@veltaholdings.com
      </li>
      <li>
        <svg viewBox="0 0 24 24" fill="none" stroke="#fff" stroke-width="2"><circle cx="12" cy="12" r="10"/><path d="M2 12h20M12 2c3 3 3 17 0 20M12 2c-3 3-3 17 0 20"/></svg>
        www.veltaholdings.com
      </li>
    </ul>
  </div>
</section>

<section class="card card--back" aria-label="Business card back">
  <p class="back__web">www.veltaholdings.com</p>
  <div class="back__brand">
    <span class="brand-dot"></span>
    <span class="brand-name">VELTA Holdings</span>
  </div>
</section>

</body>
</html>
```